Simple Business Card Design for Tavlo

Job:

Make a very simple, minimalist business card design with my details including adjusted logo. One side to be white (with logo & text). Other side to be yellow - try plain or with logo (or part of logo eg Z). Need business card to have continuity with website.

Logo:
Our logo is made from a free download font website:
http://www.typewell.net/search.php?q=rubber
but the spacing/kerning needs correcting/adjusting as the font spaces unevenly between letters (see attached files). Need logo to be very crisp/sharp when printed.

Printing:
We will be using Plika.com so the design needs to conform to their requirements, see here:

http://uk.plika.com/products/luxe/business-cards.html (scroll down for dimensions and guidelines)

Design:

must say "plant-based food consulting" underneath logo or somewhere
no address needed in contact section
sharp corners (not rounded)
one side white, one side yellow

name: Rosalind Whitcombe
1xmobile number: +44 7700900463
1xtwiiter: @brimcounsel
website address www.orchardtable.com
email address brim@orchardtable.com

Should be easy quick job, prompt + detailed feedback given, am online in UK 9am-10pm for next 3 days. Website is www.orchardtable.com

Industry/Entity Type

Business

Requirements
Must have
• The logo must be corrected. The kerning is not right.

Please use a warm-grey for text

Please submit in matt format, we will be printing matt finish.

Should not have
• Avoid using banners or curvy highlights

Please avoid using black

Please avoid submitting in gloss finish

```html
<!DOCTYPE html>
<html lang="en">
<head>
<meta charset="utf-8">
<title>Brim Business Card</title>
<link href="https://fonts.googleapis.com/css2?family=Cinzel:wght@400;700&display=swap" rel="stylesheet">
<style>
  :root {
    --backdrop: #e4e4e4;
    --card-white: #ffffff;
    --card-yellow: #ebe13e;
    --warm-grey: #6f6a64;
    --warm-grey-deep: #57524c;
    --card-line: #d6d3cf;
  }
  * { margin: 0; padding: 0; box-sizing: border-box; }
  html, body { width: 1200px; height: 720px; overflow: hidden; }
  body {
    background: var(--backdrop);
    font-family: "Cinzel", serif;
    position: relative;
  }
  .card {
    position: absolute;
    top: 242px;
    width: 420px;
    height: 240px;
  }
  .card--front {
    left: 147px;
    background: var(--card-white);
    outline: 1px solid var(--card-line);
  }
  .card--back {
    left: 633px;
    background: var(--card-yellow);
  }

  .holder {
    position: absolute;
    left: 27px;
    top: 106px;
  }
  .holder__name {
    color: var(--warm-grey-deep);
    font-weight: 700;
    font-size: 13px;
    letter-spacing: 0.02em;
    line-height: 1;
  }
  .holder__role {
    color: var(--warm-grey);
    font-size: 9.5px;
    line-height: 1;
    margin-top: 4px;
    letter-spacing: 0.03em;
  }

  .contact {
    position: absolute;
    left: 233px;
    top: 95px;
    list-style: none;
  }
  .contact__item {
    display: flex;
    align-items: center;
    gap: 8px;
    height: 13px;
    color: var(--warm-grey);
    font-size: 9px;
    letter-spacing: 0.01em;
    text-transform: uppercase;
  }
  .contact__item .num { text-transform: none; }
  .contact__icon { width: 10px; height: 9px; flex: none; }

  .brand {
    position: absolute;
    inset: 0;
    display: flex;
    flex-direction: column;
    align-items: center;
    justify-content: center;
  }
  .brand__name {
    color: var(--warm-grey-deep);
    font-weight: 700;
    font-size: 66px;
    line-height: 1;
    letter-spacing: 0.06em;
  }
  .brand__tagline {
    margin-top: 12px;
    color: var(--warm-grey-deep);
    font-size: 11px;
    letter-spacing: 0.14em;
    text-transform: uppercase;
  }
</style>
</head>
<body>
  <section class="card card--front">
    <div class="holder">
      <p class="holder__name">Rosalind Whitcombe</p>
      <p class="holder__role">Manager</p>
    </div>
    <ul class="contact">
      <li class="contact__item">
        <svg class="contact__icon" viewBox="0 0 10 9" aria-hidden="true">
          <path d="M1 3 Q5 0 9 3 L8 4 L6.5 3 L3.5 3 L2 4 Z M2.5 5 H7.5 V8.5 H2.5 Z" fill="var(--warm-grey)"/>
        </svg>
        <span class="num">+44 7700 900463</span>
      </li>
      <li class="contact__item">
        <svg class="contact__icon" viewBox="0 0 10 9" aria-hidden="true">
          <rect x="0.5" y="1" width="9" height="7" fill="var(--warm-grey)"/>
          <path d="M0.5 1 L5 5 L9.5 1 M0.5 8 L4 4.2 M9.5 8 L6 4.2" stroke="var(--card-white)" stroke-width="0.9" fill="none"/>
        </svg>
        <span>brim@orchardtable.com</span>
      </li>
      <li class="contact__item">
        <svg class="contact__icon" viewBox="0 0 10 9" aria-hidden="true">
          <rect x="0.8" y="0.8" width="8.4" height="5.6" fill="none" stroke="var(--warm-grey)" stroke-width="1.3"/>
          <rect x="3" y="7.3" width="4" height="1.2" fill="var(--warm-grey)"/>
        </svg>
        <span>www.orchardtable.com</span>
      </li>
      <li class="contact__item">
        <svg class="contact__icon" viewBox="0 0 10 9" aria-hidden="true">
          <circle cx="5" cy="4.5" r="3.6" fill="var(--warm-grey)"/>
        </svg>
        <span class="num">@brimcounsel</span>
      </li>
    </ul>
  </section>

  <section class="card card--back">
    <div class="brand">
      <span class="brand__name">BRIM</span>
      <span class="brand__tagline">plant-based food consulting</span>
    </div>
  </section>
</body>
</html>
```